corvale institute of business and technology web site

I need web site for the institute which focus on business courses and computer course it is also for vocation train for employment It is also carear development and advancement .It should have links to online study resource which free
Industry/Entity Type
Business
Number of Pages Required
1 page
Look and feel
Each slider illustrates characteristics of the customer's brand and the style your logo design should communicate.

```html
<!DOCTYPE html>
<html lang="en">
<head>
<meta charset="utf-8">
<title>Corvale Institute of Business and Technology</title>
<link href="https://fonts.googleapis.com/css2?family=Open+Sans:ital,wght@0,400;0,600;0,700;0,800;1,400&display=swap" rel="stylesheet">
<style>
:root{
  --blue:#1f74c0;
  --blue-dark:#17589a;
  --navy:#1c3550;
  --hero:#cfe5f6;
  --ink:#333a40;
  --muted:#6b737a;
  --line:#d9dee2;
  --card:#eceff2;
  --footer:#3b4147;
  --footer-deep:#30353a;
  --orange:#f5a31c;
  --green:#8cba2f;
  --white:#ffffff;
}
*{box-sizing:border-box;margin:0;padding:0}
html,body{width:1200px;height:3100px;overflow:hidden}
body{font-family:"Open Sans",Arial,sans-serif;color:var(--ink);background:var(--white);position:relative}
.abs{position:absolute}
/* header */
.topbar{left:0;top:0;width:1200px;height:150px;border-bottom:4px solid var(--blue)}
.brand{left:40px;top:22px;display:flex;align-items:center;gap:14px}
.brand-mark{width:64px;height:64px;background:var(--blue)}
.brand-name{font-weight:800;font-size:40px;color:var(--blue);line-height:1;letter-spacing:1px}
.brand-sub{font-weight:800;font-size:13px;color:var(--blue);letter-spacing:.5px;margin-top:4px}
.contact-strip{left:560px;top:12px;display:flex;gap:40px;font-size:14px;font-weight:700;color:var(--blue)}
.contact-strip div{display:flex;flex-direction:column}
.contact-strip span.val{color:var(--ink);font-weight:600;font-size:14px}
.contact-strip .lbl{display:flex;align-items:center;gap:8px}
.socials{right:40px;top:12px;display:flex;gap:8px}
.socials i,.foot-social i{display:block;width:24px;height:24px;border-radius:50%;background:var(--blue)}
.search{right:40px;top:48px;width:220px;height:30px;border:1px solid var(--line);font-size:13px;color:var(--muted);padding:5px 10px}
.nav{right:40px;top:106px;display:flex;font-size:14px;font-weight:700;color:var(--navy)}
.nav a{padding:8px 16px;border-right:2px solid var(--blue);text-decoration:none;color:inherit}
.nav a:last-child{border-right:0}
/* hero */
.hero{left:50px;top:176px;width:1100px;height:410px;background:var(--hero)}
.hero h1{position:absolute;left:70px;top:60px;width:500px;font-size:46px;line-height:1.15;font-weight:700;color:var(--blue)}
.hero p{position:absolute;left:70px;top:190px;width:470px;font-size:18px;font-weight:800;color:var(--blue-dark);line-height:1.35}
.btn-dark{position:absolute;left:70px;top:300px;background:var(--navy);color:var(--white);font-size:14px;font-weight:700;padding:14px 24px}
.hero-art{position:absolute;left:560px;top:20px;width:490px;height:370px;background:radial-gradient(circle at 50% 55%,#ffffff 0,#e3f0fa 50%,var(--hero) 75%)}
.arrow{position:absolute;top:180px;width:30px;height:40px;background:var(--navy);display:flex;align-items:center;justify-content:center}
/* welcome */
.welcome{left:50px;top:660px;width:700px}
.welcome h2{font-size:22px;font-weight:700;color:var(--blue);line-height:1.25}
.welcome p{margin-top:18px;font-size:14px;line-height:1.6;color:var(--ink)}
.video{left:800px;top:660px;width:330px;height:310px;border:1px solid var(--line)}
.video h3{font-size:18px;font-weight:700;color:var(--navy);padding:12px 14px;border-bottom:3px solid var(--blue)}
.video-shot{margin:14px;height:180px;background:linear-gradient(135deg,#5f7f9c,#a8bccb);display:flex;align-items:center;justify-content:center}
.video p{padding:0 14px;font-size:13px;color:var(--muted);line-height:1.5}
/* programs */
.programs{left:50px;top:1010px;width:1100px}
.section-head{display:flex;justify-content:space-between;align-items:center;border-bottom:3px solid var(--blue);padding-bottom:8px}
.section-head h2{font-size:18px;font-weight:800;color:var(--navy)}
.cards{display:flex;gap:20px;margin-top:20px}
.card{position:relative;width:260px;height:310px;background:var(--card);padding:14px}
.card h4{font-size:14px;font-weight:700;color:var(--navy);height:40px;line-height:1.35}
.card .shot{height:130px;margin:8px 0 12px}
.card p{font-size:12.5px;color:var(--muted);line-height:1.5}
.card .corner{position:absolute;right:0;bottom:0;width:0;height:0;border-left:28px solid transparent;border-bottom:28px solid var(--blue)}
/* banner */
.banner{left:0;top:1410px;width:1200px;height:470px;background:linear-gradient(180deg,#ece9e2 0,#d8d3c8 55%,#b9a890 100%)}
.banner h2{position:absolute;left:230px;top:175px;font-size:54px;line-height:1.05;font-weight:800;color:#2a2e33}
.banner h2 small{display:block;font-size:34px;font-weight:700}
.btn-orange{position:absolute;left:300px;top:310px;background:var(--orange);color:var(--white);font-size:26px;font-weight:800;padding:8px 30px;border-radius:4px}
.banner-desk{position:absolute;left:760px;top:120px;width:380px;height:300px;background:linear-gradient(160deg,#6f6a63,#3b3a39)}
/* testimonials */
.say{left:50px;top:1980px;width:610px;text-align:center}
.say h3{font-size:16px;font-weight:800;color:var(--navy)}
.quote-badge{width:60px;height:60px;border-radius:50%;background:var(--blue);margin:22px auto;display:flex;align-items:center;justify-content:center;color:var(--white);font-size:44px;font-weight:800;line-height:1}
.say blockquote{font-style:italic;font-size:14px;line-height:1.6;color:var(--muted);padding:0 20px}
.person{display:flex;align-items:center;justify-content:center;gap:12px;margin-top:22px;text-align:left}
.avatar{width:44px;height:44px;border-radius:50%;background:#c9a98e}
.person b{display:block;font-size:14px;color:var(--navy)}
.person span{font-size:12px;color:var(--muted)}
.alerts{left:50px;top:2330px;width:610px;height:160px;background:var(--card);text-align:center;padding-top:22px}
.alerts h3{font-size:20px;font-weight:800;color:var(--blue)}
.alerts p{font-size:13px;color:var(--muted);margin-top:4px}
.subscribe{display:flex;justify-content:center;margin-top:20px}
.subscribe span{width:320px;height:40px;background:var(--white);border:1px solid var(--line);font-size:13px;color:var(--muted);padding:10px;text-align:left}
.subscribe b{background:var(--blue);color:var(--white);font-size:14px;padding:10px 22px}
.ask{left:700px;top:1980px;width:450px;height:510px;background:var(--blue-dark)}
.ask h3{background:var(--blue);color:var(--white);font-size:18px;font-weight:800;text-align:center;padding:16px}
.ask form{padding:18px 26px}
.ask label{display:block;color:var(--white);font-size:13px;font-weight:700;margin:10px 0 5px}
.field{background:var(--white);height:34px;font-size:13px;color:var(--muted);padding:8px 10px}
.row{display:flex;gap:12px}
.row .field{flex:1}
.area{height:90px}
.submit{margin-top:18px;background:var(--green);color:var(--white);font-size:20px;font-weight:800;text-align:center;padding:10px}
/* footer */
.footer{left:0;top:2540px;width:1200px;height:560px;background:var(--footer);color:#c7ccd1}
.cols{position:absolute;left:50px;top:40px;width:1100px;display:flex;gap:40px}
.col{width:245px}
.col h5{font-size:15px;font-weight:800;color:var(--white);margin-bottom:14px}
.col li{list-style:none;font-size:13px;line-height:1.9}
.news li{margin-bottom:10px;line-height:1.45}
.news em{display:block;font-style:normal;color:#8cc3ef;font-size:12px}
.footer-bottom{position:absolute;left:0;top:420px;width:1200px;height:140px;background:var(--footer-deep)}
.partner{position:absolute;left:50px;top:30px;display:flex;align-items:center;gap:18px;color:var(--white);font-weight:800;font-size:16px;line-height:1.3}
.partner-badge{width:130px;height:80px;background:#111}
.foot-social{position:absolute;right:50px;top:40px;display:flex;gap:8px}
.copy{position:absolute;right:50px;top:85px;font-size:12px;color:#aab0b6}
</style>
</head>
<body>

<header class="abs topbar">
  <div class="abs brand">
    <div class="brand-mark"></div>
    <div>
      <div class="brand-name">CORVALE</div>
      <div class="brand-sub">INSTITUTE OF BUSINESS &amp; TECHNOLOGY</div>
    </div>
  </div>
  <div class="abs contact-strip">
    <div>
      <span class="lbl"><svg width="16" height="16" viewBox="0 0 24 24"><path fill="#1f74c0" d="M6.6 10.8a15 15 0 006.6 6.6l2.2-2.2a1 1 0 011-.25 11.4 11.4 0 003.6.6 1 1 0 011 1V20a1 1 0 01-1 1A17 17 0 013 4a1 1 0 011-1h3.5a1 1 0 011 1c0 1.25.2 2.45.6 3.6a1 1 0 01-.25 1z"/></svg>CALL US</span>
      <span class="val">+260 211 555 018</span>
    </div>
    <div>
      <span class="lbl"><svg width="16" height="16" viewBox="0 0 24 24"><rect x="2" y="5" width="20" height="14" fill="#1f74c0"/><path d="M2 5l10 8 10-8" stroke="#fff" stroke-width="2" fill="none"/></svg>EMAIL US</span>
      <span class="val">info@corvaleinstitute.example</span>
    </div>
  </div>
  <div class="abs socials"><i></i><i></i><i></i><i></i></div>
  <div class="abs search">Search</div>
  <nav class="abs nav"><a>HOME</a><a>ABOUT US</a><a>COURSES</a><a>CONTACT US</a></nav>
</header>

<section class="abs hero">
  <h1>LOREM IPSUM DOLOR SIT AMET</h1>
  <p>LOREM IPSUM DOLOR SIT AMET, CONSECTETUR ADIPISCING ELIT, SED DO EIUSMOD TEMPOR.</p>
  <span class="btn-dark">LEARN MORE</span>
  <div class="hero-art" role="img" aria-label="Illustration of a laptop surrounded by charts, graphs and learning icons"></div>
  <div class="arrow" style="left:0"><svg width="12" height="16" viewBox="0 0 12 16"><path d="M10 1L3 8l7 7" stroke="#fff" stroke-width="3" fill="none"/></svg></div>
  <div class="arrow" style="right:0"><svg width="12" height="16" viewBox="0 0 12 16"><path d="M2 1l7 7-7 7" stroke="#fff" stroke-width="3" fill="none"/></svg></div>
</section>

<section class="abs welcome">
  <h2>WELCOME TO<br>CORVALE INSTITUTE OF BUSINESS AND TECHNOLOGY</h2>
  <p>Corvale Institute of Business and Technology is a fast growing education and training provider focusing on holistic knowledge and skills interventions that impact livelihoods. It is established on the core values of making a meaningful and measurable difference in career aspirations and goals through innovative learning and knowledge management. We prepare students not only for professional careers but also inculcate the importance of discipline and equip them physically, mentally, socially and spiritually. The institution is licensed and registered under the national technical education and vocational training authority.</p>
</section>

<aside class="abs video">
  <h3>FEATURED VIDEO</h3>
  <div class="video-shot" role="img" aria-label="Video still of students in a classroom">
    <svg width="60" height="60" viewBox="0 0 60 60"><circle cx="30" cy="30" r="28" fill="#1f74c0"/><path d="M24 18l18 12-18 12z" fill="#fff"/></svg>
  </div>
  <p>Lorem ipsum dolor sit amet, consectetur adipiscing elit.</p>
</aside>

<section class="abs programs">
  <div class="section-head">
    <h2>PROGRAMS OFFERED</h2>
    <svg width="50" height="18" viewBox="0 0 50 18"><path d="M12 2L5 9l7 7M38 2l7 7-7 7" stroke="#6b737a" stroke-width="3" fill="none"/></svg>
  </div>
  <div class="cards">
    <div class="card"><h4>University Education – Long Distance Learning</h4><div class="shot" role="img" aria-label="Photo of a graduate in cap and gown" style="background:linear-gradient(135deg,#2f4f6e,#8aa3b8)"></div><p>Lorem ipsum dolor sit amet, consectetur adipiscing elit, sed do eiusmod tempor incididunt ut labore et dolore magna aliqua. Ut enim ad minim.</p><span class="corner"></span></div>
    <div class="card"><h4>Modular Soft Skills</h4><div class="shot" role="img" aria-label="Photo of a team meeting around a table" style="background:linear-gradient(135deg,#6d7c86,#c4ccd1)"></div><p>Lorem ipsum dolor sit amet, consectetur adipiscing elit, sed do eiusmod tempor incididunt ut labore et dolore magna aliqua. Ut enim ad minim.</p><span class="corner"></span></div>
    <div class="card"><h4>Direct to Degree (D2D)</h4><div class="shot" role="img" aria-label="Illustration of digital learning icons on blue" style="background:linear-gradient(135deg,#1b5e9e,#5fb0e6)"></div><p>Lorem ipsum dolor sit amet, consectetur adipiscing elit, sed do eiusmod tempor incididunt ut labore et dolore magna aliqua. Ut enim ad minim.</p><span class="corner"></span></div>
    <div class="card"><h4>Brightpath</h4><div class="shot" role="img" aria-label="Photo of a professional in an office" style="background:linear-gradient(135deg,#9db4c6,#e3e9ee)"></div><p>Lorem ipsum dolor sit amet, consectetur adipiscing elit, sed do eiusmod tempor incididunt ut labore et dolore magna aliqua. Ut enim ad minim.</p><span class="corner"></span></div>
  </div>
</section>

<section class="abs banner" role="img" aria-label="Photo of a study desk with a laptop, lamp and books">
  <h2>ONLINE STUDY<small>RESOURCE WHICH FREE</small></h2>
  <span class="btn-orange">CLICK HERE</span>
  <div class="banner-desk"></div>
</section>

<section class="abs say">
  <h3>WHAT OUR PEOPLE SAY</h3>
  <div class="quote-badge">&ldquo;</div>
  <blockquote>"Lorem ipsum dolor sit amet, consectetur adipiscing elit, sed do eiusmod tempor incididunt ut labore et dolore magna aliqua. Ut enim ad minim veniam, quis nostrud exercitation ullamco laboris nisi ut aliquip ex ea commodo consequat."</blockquote>
  <div class="person">
    <div class="avatar" role="img" aria-label="Portrait of the student"></div>
    <div><b>Lena Morrow</b><span>Lorem ipsum dolor</span></div>
  </div>
</section>

<section class="abs alerts">
  <h3>AUCTION ALERTS!</h3>
  <p>Sign up to receive email alerts about our upcoming auctions</p>
  <div class="subscribe"><span>Enter your email address</span><b>Subscribe</b></div>
</section>

<section class="abs ask">
  <h3>DO YOU HAVE A QUESTION?</h3>
  <form>
    <label>Your Name*</label>
    <div class="row"><div class="field">First Name</div><div class="field">Last Name</div></div>
    <label>Email*</label>
    <div class="field">Your Email Address here</div>
    <label>Phone</label>
    <div class="field">Phone Number</div>
    <label>Comments*</label>
    <div class="field area"></div>
    <div class="submit">SUBMIT</div>
  </form>
</section>

<footer class="abs footer">
  <div class="cols">
    <div class="col"><h5>NAVIGATION</h5><ul><li>Home</li><li>About Us</li><li>Courses</li><li>Contact Us</li></ul></div>
    <div class="col"><h5>PROGRAMS OFFERED</h5><ul><li>University Education – Long Distance Learning</li><li>Modular Soft Skills</li><li>Direct to Degree (D2D)</li><li>Brightpath</li><li>Technology Skills in the Talent Curriculum</li><li>Business Domain Technology Capabilities</li></ul></div>
    <div class="col news"><h5>RECENT NEWS</h5><ul><li><em>January 18, 2024</em>Lorem ipsum dolor sit amet, consectetur adipiscing elit</li><li><em>January 22, 2024</em>Lorem ipsum dolor sit amet, consectetur adipiscing elit</li><li><em>January 27, 2024</em>Lorem ipsum dolor sit amet, consectetur adipiscing elit</li></ul></div>
    <div class="col"><h5>CONTACT INFO</h5><ul><li>Plot 42 Cedar Park Complex, Northgate, Lusaka</li><li>Phone: +260 211 555 018</li><li>Mobile: +260 977 555 204</li><li>info@corvaleinstitute.example</li></ul></div>
  </div>
  <div class="footer-bottom">
    <div class="partner"><span>IN CONJUNCTION<br>WITH BRIGHTPATH</span><div class="partner-badge"></div></div>
    <div class="foot-social"><i></i><i></i><i></i><i></i></div>
    <div class="copy">© 2024 Corvale Institute of Business and Technology. All Rights Reserved.</div>
  </div>
</footer>

</body>
</html>
```